Dentistry

Dentist's personal business card. No logo needed. The card shoul deliver the massage of reliability, professionalism, experience.
Please ad the full brief of the project: down the line it says: the winning look should be precise and pristine NO pictures of Teeth, smiles, instruments etc.

The details to be desplaid are:
Dr. Rob Tavolen
Doctor of Dental Surgery
PHD
Web. Www.drtavolen.com
Email. Rob@drtavolen.com
Tel 07742318590
Surgery address. 27Bferndale road London SW4 8QT UK
62 Wexley Row London SW3 2HN. Uk

Reason: Decided to make the payment unrefundable in order to get more designers involved.

Requirements
Should not have
• Logo, teeth, smile any sort of instruments.

```html
<!DOCTYPE html>
<html lang="en">
<head>
<meta charset="utf-8">
<title>Dr Rob Tavolen — Business Card</title>
<link rel="stylesheet" href="https://fonts.googleapis.com/css2?family=Orbitron:wght@400;700&display=swap">
<style>
  :root {
    --backdrop: #4b4b4d;
    --card-top: #f7f6f2;
    --card-mid: #e7e1d6;
    --card-bottom: #f4f2ee;
    --ornament-soft: rgba(255, 255, 255, 0.35);
    --ornament-clear: rgba(255, 255, 255, 0);
    --ink: #8f8378;
    --ink-strong: #6f655c;
  }
  * { margin: 0; padding: 0; box-sizing: border-box; }
  html, body {
    width: 1200px; height: 999px; overflow: hidden;
    background: var(--backdrop);
    font-family: "Orbitron", sans-serif;
    color: var(--ink);
  }
  .canvas { position: relative; width: 1200px; height: 999px; }
  .card {
    position: absolute;
    width: 485px; height: 296px;
    border-radius: 16px;
    overflow: hidden;
    background: linear-gradient(180deg, var(--card-top) 0%, var(--card-mid) 55%, var(--card-bottom) 100%);
  }
  .card--front { left: 155px; top: 199px; }
  .card--back { left: 563px; top: 530px; }

  .ornament { position: absolute; }
  .ornament--front {
    left: 85px; top: 0; width: 305px; height: 296px;
    background: linear-gradient(90deg, var(--ornament-clear) 0%, var(--ornament-soft) 50%, var(--ornament-clear) 100%);
  }
  .ornament--back {
    left: 0; top: 40px; width: 485px; height: 180px;
    background: linear-gradient(180deg, var(--ornament-clear) 0%, var(--ornament-soft) 50%, var(--ornament-clear) 100%);
  }

  .front__name {
    position: absolute; left: 112px; top: 140px;
    font-size: 21px; letter-spacing: 2.4px; text-transform: uppercase;
    color: var(--ink);
  }
  .back__title {
    position: absolute; left: 0; right: 0; top: 14px;
    text-align: center; font-size: 20px; font-weight: 400; letter-spacing: 2.6px;
    text-transform: uppercase; color: var(--ink);
  }
  .back__degree {
    position: absolute; left: 0; right: 0; top: 48px;
    text-align: center; font-size: 16px; font-weight: 700; letter-spacing: 2px;
    color: var(--ink-strong);
  }
  .contact {
    position: absolute; display: flex; align-items: center; gap: 7px;
    color: var(--ink-strong); white-space: nowrap;
  }
  .contact svg { width: 15px; height: 15px; fill: var(--ink-strong); flex: none; }
  .contact--address { left: 30px; top: 199px; font-size: 13.5px; }
  .contact--phone { left: 30px; top: 226px; font-size: 12px; }
  .contact--branch { left: 205px; top: 229px; font-size: 9px; }
  .contact--web { left: 30px; top: 252px; font-size: 14.5px; }
  .contact--email { left: 252px; top: 252px; font-size: 14.5px; }
</style>
</head>
<body>
<main class="canvas">
  <section class="card card--front" aria-label="Card front">
    <div class="ornament ornament--front" role="img" aria-label="Fine white line-art wave running vertically across the card"></div>
    <p class="front__name">Dr Rob Tavolen</p>
  </section>

  <section class="card card--back" aria-label="Card back">
    <div class="ornament ornament--back" role="img" aria-label="Fine white line-art wave running horizontally across the card"></div>
    <h1 class="back__title">Doctor of Dental Surgery</h1>
    <p class="back__degree">PHD</p>

    <p class="contact contact--address">
      <svg viewBox="0 0 16 16" aria-hidden="true"><path d="M8 1 L15 8 H13 V15 H10 V10 H6 V15 H3 V8 H1 Z"/></svg>
      27Bferndale road london sw4 8qt uk
    </p>
    <p class="contact contact--phone">
      <svg viewBox="0 0 16 16" aria-hidden="true"><path d="M4 1 H12 V15 H4 Z M5.5 2.5 V9 H10.5 V2.5 Z M6 10.5 H7.5 V12 H6 Z M8.5 10.5 H10 V12 H8.5 Z"/></svg>
      07742318590
    </p>
    <p class="contact contact--branch">62 wexley row london sw3 2hn uk</p>
    <p class="contact contact--web">
      <svg viewBox="0 0 16 16" aria-hidden="true"><path d="M8 1 A7 7 0 1 0 8.01 1 Z M8 2.5 A5.5 5.5 0 1 1 7.99 2.5 Z M7.3 2 H8.7 V14 H7.3 Z M2 7.3 H14 V8.7 H2 Z"/></svg>
      www.drtavolen.com
    </p>
    <p class="contact contact--email">
      <svg viewBox="0 0 16 16" aria-hidden="true"><path d="M1 3 H15 V13 H1 Z M2.5 4.5 L8 9 L13.5 4.5 Z"/></svg>
      rob@drtavolen.com
    </p>
  </section>
</main>
</body>
</html>
```